Business card

We need a business card design for our company based in Auckland , New Zealand called 'Ridge + Studio Ltd'. We provide architectural services. We would like to see designs that use the max. three colours (such as white, black, grey) The final design should communicate financial safety and growth."
Also I will provide our company logo. I would like to the logo to be embeded onto our business card.

Target Market(s)

new residential house, alteration & addition & light commericila design & drafting service

Industry/Entity Type

Architecture

Contact Information for Business Card

Company name: ridge + studio Ltd.
Name: Mark Delford
Job title: architectural designer & Design LBP
email address: mark@rplusd.co.nz
mobile number: 02 5163 2290
web site: www.rplusd.co.nz

Requirements
Must have
• My project must have..
• - embeded logo (attached company logo)
• I don't have a bigger version for our company logo, but I have one old one, so you can remove the word from it)
• - insert the attached small BKTW logo & LBP logo
• - creative, simple and clear business card.
• - Max. three colours
Nice to have
• - Here are the samples I would like to share with you: http://www.plimvora.com/blog/minimalistic-business-card-designs/
• I would like to have my business card like one of the creation.
Should not have
• TBA

```html
<!DOCTYPE html>
<html lang="en">
<head>
<meta charset="utf-8">
<title>Ridge + Studio Ltd — Business Card</title>
<link href="https://fonts.googleapis.com/css2?family=Questrial&family=Source+Sans+3:wght@400;600&display=swap" rel="stylesheet">
<style>
  :root {
    --page: #2f2a27;
    --card: #0b0b0b;
    --accent: #ef9224;
    --silver: #b9b9b9;
    --text: #d6d6d6;
    --rule: #2a2a2a;
  }
  * { box-sizing: border-box; margin: 0; padding: 0; }
  html, body { width: 1200px; height: 900px; overflow: hidden; }
  body {
    background: var(--page);
    font-family: "Source Sans 3", "Helvetica Neue", Arial, sans-serif;
    position: relative;
  }
  .card {
    position: absolute;
    top: 302px;
    width: 520px;
    height: 297px;
    background: var(--card);
    box-shadow: 0 10px 30px rgba(0,0,0,.45);
  }
  .card--front { left: 60px; }
  .card--back { left: 620px; }

  /* Front */
  .brand {
    position: absolute;
    left: 30px;
    top: 0;
    width: 225px;
    height: 297px;
    display: flex;
    align-items: center;
    justify-content: center;
    gap: 10px;
  }
  .brand__square {
    width: 14px;
    height: 14px;
    background: var(--accent);
    flex: none;
  }
  .brand__name {
    font-family: "Questrial", "Century Gothic", sans-serif;
    color: var(--accent);
    font-size: 21px;
    white-space: nowrap;
  }
  .divider {
    position: absolute;
    left: 255px;
    top: 70px;
    width: 1px;
    height: 150px;
    background: var(--rule);
  }
  .person {
    position: absolute;
    left: 282px;
    top: 78px;
  }
  .person__name {
    color: var(--accent);
    font-weight: 600;
    font-size: 17px;
    line-height: 1.1;
  }
  .person__title {
    color: var(--text);
    font-size: 13px;
    margin-top: 2px;
  }
  .contact {
    list-style: none;
    margin-top: 38px;
  }
  .contact__item {
    display: flex;
    align-items: center;
    gap: 9px;
    color: var(--text);
    font-size: 13.5px;
    line-height: 19px;
  }
  .contact__icon { width: 10px; height: 10px; flex: none; }

  /* Back */
  .logo-block {
    position: absolute;
    left: 0; right: 0;
    top: 150px;
    display: flex;
    justify-content: center;
    align-items: center;
    gap: 12px;
  }
  .logo-block__square {
    width: 16px;
    height: 16px;
    background: var(--silver);
    flex: none;
  }
  .logo-block__name {
    font-family: "Questrial", "Century Gothic", sans-serif;
    color: var(--silver);
    font-size: 22px;
    letter-spacing: .3px;
  }
  .badges {
    position: absolute;
    left: 0; right: 0;
    top: 212px;
    display: flex;
    justify-content: center;
    align-items: center;
    gap: 34px;
  }
  .badge-member { display: flex; flex-direction: column; align-items: flex-start; }
  .badge-member__shape {
    width: 44px;
    height: 24px;
    background: var(--silver);
  }
  .badge-member__caption {
    color: var(--silver);
    font-size: 10px;
    line-height: 11px;
    margin-top: 3px;
  }
  .badge-practitioner {
    width: 50px;
    height: 50px;
    border-radius: 50%;
    background: var(--silver);
  }
</style>
</head>
<body>

  <section class="card card--front" aria-label="Business card front">
    <div class="brand">
      <span class="brand__square" aria-hidden="true"></span>
      <span class="brand__name">ridge + studio</span>
    </div>
    <div class="divider"></div>
    <div class="person">
      <p class="person__name">Mark Delford</p>
      <p class="person__title">Architectural designer &amp; Design LBP</p>
      <ul class="contact">
        <li class="contact__item">
          <svg class="contact__icon" viewBox="0 0 10 10" aria-hidden="true"><path d="M2 0.5 L3.8 2.6 L2.9 3.8 Q4 6 6.2 7.1 L7.4 6.2 L9.5 8 L8.3 9.5 Q3.5 9 0.5 1.7 Z" fill="var(--accent)"/></svg>
          02 5163 2290
        </li>
        <li class="contact__item">
          <svg class="contact__icon" viewBox="0 0 10 10" aria-hidden="true"><rect x="0.5" y="2" width="9" height="6.5" fill="var(--accent)"/><path d="M0.8 2.3 L5 5.6 L9.2 2.3" stroke="var(--card)" stroke-width="0.9" fill="none"/></svg>
          mark@rplusd.co.nz
        </li>
        <li class="contact__item">
          <svg class="contact__icon" viewBox="0 0 10 10" aria-hidden="true"><circle cx="5" cy="5" r="4.5" fill="var(--accent)"/><path d="M0.5 5 H9.5 M5 0.5 Q2.5 5 5 9.5 M5 0.5 Q7.5 5 5 9.5" stroke="var(--card)" stroke-width="0.7" fill="none"/></svg>
          www.rplusd.co.nz
        </li>
      </ul>
    </div>
  </section>

  <section class="card card--back" aria-label="Business card back">
    <div class="logo-block">
      <span class="logo-block__square" aria-hidden="true"></span>
      <p class="logo-block__name">ridge + studio Ltd.</p>
    </div>
    <div class="badges">
      <div class="badge-member">
        <div class="badge-member__shape" role="img" aria-label="BKTW membership badge"></div>
        <p class="badge-member__caption">Professional<br>Member</p>
      </div>
      <div class="badge-practitioner" role="img" aria-label="Licensed building practitioner badge"></div>
    </div>
  </section>

</body>
</html>
```